Velvet Meadow Hamper company needs a brochure design

We need a brochure design for a new company in Dubai called 'Velvet Meadow Hampers'. We already have a logo designed which I have attached and would like to use this and the green/gold/white colours for our brochure. Our company initially will be supplying Velvet Meadow Hamper wear of traditional wicker baskets in many designs which hold all the cutlery, crockery and accessories. We will also be selling picnic accessories. We want to purvey a sense of luxury and class in line with our logo. I have attached some photos of the picnicwear. As our products are changing all the time I thought a fold out cover which stays the same and then product cards inserted into the folder which can be changed according to our product changes. I am looking for a fairly simple design and each product card should have at least one photo of the product on it with a spec and description also. On the cover of the folder I would like room to write about the company and what we do, this can be inside or out and may or may not include photos. I have the logo designs in illustrator format and pdf. Please contact if any more information is needed.
Updates

Reason: I have extended this deadline as there are some content changes taking place.

Industry/Entity Type

It Company

```html
<!DOCTYPE html>
<html lang="en">
<head>
<meta charset="utf-8">
<title>Velvet Meadow Hampers – Folder Cover</title>
<link rel="stylesheet" href="https://fonts.googleapis.com/css2?family=Libre+Baskerville&family=Montserrat:wght@600&display=swap">
<style>
  :root {
    --paper: #ffffff;
    --meadow: #1c3a21;
    --meadow-light: #2c4b2e;
    --gold: #c9a24c;
    --gold-dark: #7a4a1e;
    --mark: #222222;
  }
  * { margin: 0; padding: 0; box-sizing: border-box; }
  html, body { width: 1200px; height: 969px; overflow: hidden; background: var(--paper); }
  .sheet { position: relative; width: 1200px; height: 969px; font-family: "Libre Baskerville", Georgia, serif; }

  .print-marks { position: absolute; inset: 0; }
  .fold-label { position: absolute; top: 0; font-family: Arial, Helvetica, sans-serif; font-size: 9px; color: var(--mark); }

  .cover-panel { position: absolute; left: 22px; top: 22px; width: 1156px; height: 728px; background: var(--meadow); }
  .pocket-flap { position: absolute; left: 131px; top: 750px; width: 556px; height: 198px; background: var(--meadow); }

  .swirl-motif {
    position: absolute; left: 153px; top: 162px; width: 220px; height: 433px;
    border-radius: 110px 110px 90px 90px;
    background: radial-gradient(ellipse at 60% 45%, var(--meadow-light) 0%, rgba(44,75,46,0.55) 55%, rgba(44,75,46,0) 80%);
  }

  .brand-name {
    position: absolute; left: 661px; width: 517px; top: 114px; text-align: center;
    font-family: "Montserrat", Arial, sans-serif; font-weight: 600; font-size: 16px;
    letter-spacing: 3.2px; color: var(--gold);
  }
  .brand-dot { display: block; width: 22px; height: 22px; margin: 0 auto 10px; border-radius: 50%; background: var(--gold); }

  .hero-photo { position: absolute; left: 661px; top: 214px; width: 517px; height: 323px; }
  .hero-band { height: 7px; background: linear-gradient(90deg, var(--gold-dark), var(--gold) 45%, #f1dd9a 60%, var(--gold-dark)); }
  .hero-scene { height: 309px; background: linear-gradient(180deg, #7d8a4c 0%, #a9ad6a 45%, #c8b27c 70%, #eeece4 85%, #f5f4ef 100%); }

  .web-address { position: absolute; font-size: 13px; color: var(--gold); text-align: center; width: 300px; }
  .web-address.back { left: 257px; top: 668px; }
  .web-address.front { left: 764px; top: 665px; }

  .flap-contact {
    position: absolute; left: 323px; top: 797px; width: 175px; height: 68px;
    transform: rotate(180deg); color: var(--gold); font-size: 9px; line-height: 13px;
  }
  .flap-contact .contact-name { font-family: "Montserrat", Arial, sans-serif; font-weight: 600; font-size: 9px; letter-spacing: 2.4px; margin-bottom: 12px; }
</style>
</head>
<body>
<div class="sheet">
  <svg class="print-marks" width="1200" height="969" viewBox="0 0 1200 969" stroke="#222" stroke-width="0.8" fill="none">
    <g>
      <circle cx="15" cy="15" r="5"/><line x1="5" y1="15" x2="25" y2="15"/><line x1="15" y1="5" x2="15" y2="25"/>
      <circle cx="1185" cy="15" r="5"/><line x1="1175" y1="15" x2="1195" y2="15"/><line x1="1185" y1="5" x2="1185" y2="25"/>
      <circle cx="15" cy="954" r="5"/><line x1="5" y1="954" x2="25" y2="954"/><line x1="15" y1="944" x2="15" y2="964"/>
      <circle cx="1185" cy="954" r="5"/><line x1="1175" y1="954" x2="1195" y2="954"/><line x1="1185" y1="944" x2="1185" y2="964"/>
      <line x1="31" y1="0" x2="31" y2="16"/><line x1="1169" y1="0" x2="1169" y2="16"/>
      <line x1="0" y1="31" x2="14" y2="31"/><line x1="1186" y1="31" x2="1200" y2="31"/>
      <line x1="31" y1="952" x2="31" y2="969"/><line x1="1169" y1="952" x2="1169" y2="969"/>
    </g>
    <g>
      <line x1="153" y1="10" x2="153" y2="20"/><polyline points="151,17 153,20 155,17"/>
      <line x1="661" y1="10" x2="661" y2="20"/><polyline points="659,17 661,20 663,17"/>
      <line x1="153" y1="950" x2="153" y2="960"/><polyline points="151,953 153,950 155,953"/>
      <line x1="661" y1="950" x2="661" y2="960"/><polyline points="659,953 661,950 663,953"/>
      <line x1="2" y1="723" x2="18" y2="723"/><polyline points="15,721 18,723 15,725"/>
      <line x1="1182" y1="723" x2="1198" y2="723"/><polyline points="1185,721 1182,723 1185,725"/>
    </g>
  </svg>
  <span class="fold-label" style="left:137px;">Side Fold</span>
  <span class="fold-label" style="left:644px;">Center Fold</span>
  <span class="fold-label" style="left:697px; top:7px;">UP</span>

  <section class="cover-panel" aria-label="Folder outer cover"></section>
  <section class="pocket-flap" aria-label="Pocket flap"></section>

  <div class="swirl-motif" role="img" aria-label="Large faint decorative swirl motif on the back cover"></div>

  <h1 class="brand-name"><span class="brand-dot"></span>VELVET MEADOW HAMPERS</h1>

  <figure class="hero-photo">
    <div class="hero-band"></div>
    <div class="hero-scene" role="img" aria-label="Photograph of an open wicker picnic hamper with cutlery and a cushion on a white blanket in front of tall grass"></div>
    <div class="hero-band"></div>
  </figure>

  <p class="web-address back">www.velvetmeadowhampers.com</p>
  <p class="web-address front">www.velvetmeadowhampers.com</p>

  <address class="flap-contact" style="font-style:normal;">
    <div class="contact-name">VELVET MEADOW HAMPERS</div>
    <div>Phone : 00 971 (0) 55 000 1234</div>
    <div>Email : hello@velvetmeadowhampers.com</div>
    <div>Web &nbsp;&nbsp;: www.velvetmeadowhampers.com</div>
  </address>
</div>
</body>
</html>
```